Local Roofing/Construction company business needs new biz card design

We need a new business card design, current cards are from the start of this operation and generic at best. We are a local Construction Company (General Contractor) with a majority of our work originating from insurance claims-exterior finish work is the main focus (Roofs-Siding-Gutters etc). Heavily involved with homeowners and the low ball offers they receive from insurance company's after a insurable event takes place. I have attached some of our original logo file(s) below.

```html
<!DOCTYPE html>
<html lang="en">
<head>
<meta charset="utf-8">
<title>Halverson Exteriors – Business Card</title>
<link href="https://fonts.googleapis.com/css2?family=Open+Sans:wght@400;600;700;800&display=swap" rel="stylesheet">
<style>
  :root {
    --stage: #232323;
    --card: #061d21;
    --card-deep: #041518;
    --green: #52bf6e;
    --white: #f4f4f0;
    --muted: #0b2a2f;
  }
  * { box-sizing: border-box; margin: 0; padding: 0; }
  html, body {
    width: 1200px; height: 780px; overflow: hidden;
    background: var(--stage);
    font-family: "Open Sans", Arial, sans-serif;
  }
  .stage { position: relative; width: 1200px; height: 780px; }

  .card {
    position: absolute;
    width: 560px; height: 320px;
    background: var(--card);
    border-bottom: 4px solid var(--green);
    border-left: 2px solid var(--green);
    box-shadow: 0 18px 40px rgba(0,0,0,.55);
    overflow: hidden;
  }
  .card--front { left: 60px; top: 60px; }
  .card--back  { left: 580px; top: 400px; }

  .wordmark {
    display: flex; align-items: center; gap: 12px;
    color: var(--green);
    font-weight: 800;
    text-transform: uppercase;
    letter-spacing: 1px;
    line-height: 1;
    white-space: nowrap;
  }
  .wordmark__square {
    width: 30px; height: 30px;
    background: var(--green);
    border-radius: 4px;
    flex: none;
  }
  .card--front .wordmark {
    position: absolute; left: 50%; top: 50%;
    transform: translate(-50%, -50%);
    font-size: 32px;
  }
  .card--front .wordmark__square { width: 44px; height: 44px; }

  .card--back .wordmark {
    position: absolute; left: 32px; top: 100px;
    font-size: 19px;
  }

  .identity {
    position: absolute; right: 40px; top: 24px;
    text-align: right;
  }
  .identity__name {
    color: var(--green);
    font-weight: 700; font-size: 24px; letter-spacing: .5px;
    line-height: 1.2;
  }
  .identity__role {
    color: var(--white);
    font-weight: 600; font-size: 13px; margin-top: 2px;
  }
  .identity-bar {
    position: absolute; right: 0; top: 22px;
    width: 22px; height: 62px;
    background: var(--green);
  }

  .backdrop-mark {
    position: absolute; right: 36px; bottom: 28px;
    width: 160px; height: 160px;
    background: var(--card-deep);
    border: 1px solid var(--muted);
    border-radius: 10px;
  }

  .contact {
    position: absolute; left: 32px; bottom: 26px;
    color: var(--white);
    font-size: 13px; line-height: 1.45;
  }
  .contact__address { margin-bottom: 10px; }
  .contact__list { list-style: none; }
  .contact__list li { display: flex; align-items: center; gap: 10px; }
  .contact__icon { width: 13px; height: 13px; flex: none; }
</style>
</head>
<body>
<main class="stage">

  <section class="card card--front" aria-label="Card front">
    <div class="wordmark">
      <span class="wordmark__square" aria-hidden="true"></span>
      <span>Halverson Exteriors</span>
    </div>
  </section>

  <section class="card card--back" aria-label="Card back">
    <div class="identity">
      <div class="identity__name">Marta Kovalenko</div>
      <div class="identity__role">Co-Founder</div>
    </div>
    <div class="identity-bar" aria-hidden="true"></div>

    <div class="wordmark">
      <span class="wordmark__square" aria-hidden="true"></span>
      <span>Halverson Exteriors</span>
    </div>

    <div class="backdrop-mark" aria-hidden="true"></div>

    <div class="contact">
      <p class="contact__address">42 Birch Hollow Dr<br>Lakeport, MO 63021</p>
      <ul class="contact__list">
        <li>
          <svg class="contact__icon" viewBox="0 0 24 24" aria-hidden="true"><path fill="#52bf6e" d="M6.6 10.8a15.1 15.1 0 0 0 6.6 6.6l2.2-2.2c.3-.3.7-.4 1-.2 1.1.4 2.3.6 3.6.6.6 0 1 .4 1 1V20c0 .6-.4 1-1 1A17 17 0 0 1 3 4c0-.6.4-1 1-1h3.5c.6 0 1 .4 1 1 0 1.3.2 2.5.6 3.6.1.3 0 .7-.2 1z"/></svg>
          555-210-4417
        </li>
        <li>
          <svg class="contact__icon" viewBox="0 0 24 24" aria-hidden="true"><path fill="#52bf6e" d="M6.6 10.8a15.1 15.1 0 0 0 6.6 6.6l2.2-2.2c.3-.3.7-.4 1-.2 1.1.4 2.3.6 3.6.6.6 0 1 .4 1 1V20c0 .6-.4 1-1 1A17 17 0 0 1 3 4c0-.6.4-1 1-1h3.5c.6 0 1 .4 1 1 0 1.3.2 2.5.6 3.6.1.3 0 .7-.2 1z"/></svg>
          555-210-8830 (Emergency)
        </li>
        <li>
          <svg class="contact__icon" viewBox="0 0 24 24" aria-hidden="true"><circle cx="12" cy="12" r="9.5" fill="none" stroke="#52bf6e" stroke-width="2.2"/><path d="M2.5 12h19M12 2.5c3 3 3 16 0 19M12 2.5c-3 3-3 16 0 19" fill="none" stroke="#52bf6e" stroke-width="1.8"/></svg>
          www.halversonexteriors.com
        </li>
        <li>
          <svg class="contact__icon" viewBox="0 0 24 24" aria-hidden="true"><rect x="2" y="5" width="20" height="14" rx="1.5" fill="none" stroke="#52bf6e" stroke-width="2.2"/><path d="M2.5 6l9.5 7 9.5-7" fill="none" stroke="#52bf6e" stroke-width="2.2"/></svg>
          office@halversonexteriors.com
        </li>
      </ul>
    </div>
  </section>

</main>
</body>
</html>
```